Harborview Estates Business Card for Apartment Buildings

Create business cards for resident managers who run apartment buildings. The audience is the public who are searching for apartment rentals, and current residents who live at the apartment building. Key design element will be incorporating the company logo, however, the logo cannot dominate. The building name and manager name are more important than the logo. Current business card design leaves little room for copy, so we may need to reduce the size on the current card to allow for more space for copy.

Target Market(s)

Adults 18-65 years of age, who are looking for an apartment rental, plus current residents who live at our apartment buildings.

Industry/Entity Type

Property Management

Contact Information for Business Card

A major design element will be use of the company logo. Important property and manager contact information must be part of the design. The size of the logo will need to be reduced to make room for building and manager contact copy.

Font styles to use
Sans Serif

Colors
3176b5
000000
959595
ffffff

Requirements
Must have
• 1) Incorporate the company logo.
• 2) Use the company colors (dark blue, black/grey, over white).
• 3) FEATURE THE BUILDING NAME
• 4) FEATURE THE MANAGER NAME
• 5) The company name is less important than BUILDING and MANAGER
• 6) Manager contact information
• **SEE ATTACHED CREATIVE BRIEF**
Nice to have
• 1) Back of card logo watermark
• 2) Ability to write notes on back of carfd
Should not have
• Avoid letting the company logo dominate the card, the building name and manager are more important than the company logo.

```html
<!DOCTYPE html>
<html lang="en">
<head>
<meta charset="utf-8">
<title>Harborview Estates – Resident Manager Card</title>
<link href="https://fonts.googleapis.com/css2?family=Lato:wght@400;700&display=swap" rel="stylesheet">
<style>
  :root {
    --brand-blue: #3176b5;
    --deep-blue: #1769ab;
    --charcoal: #3f4042;
    --card-dark: #4a4b4e;
    --mid-grey: #959595;
    --ink: #2b2b2b;
    --white: #ffffff;
    --stage: #e6e7e9;
  }
  * { margin: 0; padding: 0; box-sizing: border-box; }
  html, body { width: 1200px; height: 900px; overflow: hidden; }
  body {
    background: var(--stage);
    font-family: "Lato", Arial, sans-serif;
    position: relative;
  }
  .card {
    position: absolute;
    left: 280px;
    width: 640px;
    height: 366px;
    border-radius: 18px;
    overflow: hidden;
    box-shadow: 0 6px 18px rgba(0,0,0,0.18);
  }
  /* Back of card */
  .card-back { top: 52px; background: var(--card-dark); }
  .card-back .company-name {
    position: absolute; left: 0; right: 0; top: 128px;
    text-align: center;
    color: var(--white);
    font-weight: 700;
    font-size: 40px;
    letter-spacing: 1px;
  }
  .card-back .company-sub {
    position: absolute; left: 0; right: 0; top: 182px;
    text-align: center;
    color: var(--white);
    font-weight: 700;
    font-size: 16px;
    letter-spacing: 6px;
  }
  .card-back .back-url {
    position: absolute; left: 0; right: 0; bottom: 38px;
    text-align: center;
    color: var(--white);
    font-size: 15px;
    letter-spacing: 1px;
  }
  /* Front of card */
  .card-front { top: 470px; background: var(--white); }
  .front-brand {
    position: absolute; left: 40px; top: 120px; width: 270px;
    display: flex; align-items: center; gap: 12px;
  }
  .brand-square { width: 34px; height: 34px; background: var(--deep-blue); flex: none; }
  .brand-name {
    color: var(--deep-blue);
    font-weight: 700;
    font-size: 24px;
    line-height: 1.1;
    letter-spacing: 0.5px;
  }
  .divider {
    position: absolute; left: 340px; top: 72px;
    width: 2px; height: 200px;
    background: var(--deep-blue);
  }
  .contact {
    position: absolute; left: 362px; top: 52px; right: 20px;
    color: var(--ink);
  }
  .manager-name { color: var(--deep-blue); font-weight: 700; font-size: 25px; line-height: 1.1; }
  .manager-role { font-size: 15px; margin-bottom: 8px; }
  .building-name { color: var(--deep-blue); font-weight: 700; font-size: 20px; line-height: 1.15; }
  .address { font-size: 15px; line-height: 1.25; margin-bottom: 10px; }
  .contact-list { list-style: none; }
  .contact-list li {
    display: flex; align-items: center; gap: 10px;
    font-size: 16px; line-height: 1.5;
  }
  .contact-list svg { width: 13px; height: 13px; flex: none; }
  .wave { position: absolute; left: 0; bottom: 0; width: 640px; height: 140px; }
</style>
</head>
<body>

<section class="card card-back">
  <div class="company-name">HARBORVIEW ESTATES</div>
  <div class="company-sub">LLC</div>
  <div class="back-url">www.harborviewest.com</div>
</section>

<section class="card card-front">
  <div class="front-brand">
    <span class="brand-square"></span>
    <span class="brand-name">HARBORVIEW ESTATES LLC</span>
  </div>

  <div class="divider"></div>

  <div class="contact">
    <div class="manager-name">Marisol Quintana</div>
    <div class="manager-role">Resident Manager</div>
    <div class="building-name">Cedar Crest Apartments</div>
    <div class="address">1458 Larkspur Avenue<br>Bayside, CA 90210</div>
    <ul class="contact-list">
      <li>
        <svg viewBox="0 0 16 16"><path d="M4 1 L6.5 4 L5 6 C6 8 8 10 10 11 L12 9.5 L15 12 L13 15 C7 14 2 9 1 3 Z" fill="var(--deep-blue)"/></svg>
        555-210-4381
      </li>
      <li>
        <svg viewBox="0 0 16 16"><rect x="4" y="1" width="8" height="4" fill="var(--deep-blue)"/><rect x="1" y="6" width="14" height="6" rx="1" fill="var(--deep-blue)"/><rect x="4" y="10" width="8" height="5" fill="var(--deep-blue)"/></svg>
        555-210-4392
      </li>
      <li>
        <svg viewBox="0 0 16 16"><rect x="4" y="1" width="8" height="14" rx="1.5" fill="none" stroke="var(--deep-blue)" stroke-width="1.6"/><circle cx="8" cy="12.5" r="0.9" fill="var(--deep-blue)"/></svg>
        555-388-7146
      </li>
      <li>
        <svg viewBox="0 0 16 16"><rect x="1" y="3" width="14" height="10" fill="none" stroke="var(--deep-blue)" stroke-width="1.6"/><path d="M1 3 L8 9 L15 3" fill="none" stroke="var(--deep-blue)" stroke-width="1.6"/></svg>
        marisol@harborviewest.com
      </li>
      <li>
        <svg viewBox="0 0 16 16"><circle cx="8" cy="8" r="6.5" fill="none" stroke="var(--deep-blue)" stroke-width="1.4"/><ellipse cx="8" cy="8" rx="2.8" ry="6.5" fill="none" stroke="var(--deep-blue)" stroke-width="1.2"/><path d="M1.5 8 H14.5" stroke="var(--deep-blue)" stroke-width="1.2"/></svg>
        www.harborviewest.com
      </li>
    </ul>
  </div>

  <svg class="wave" viewBox="0 0 640 140" preserveAspectRatio="none" aria-hidden="true">
    <path d="M0 12 C120 14 220 40 330 88 C440 130 560 108 640 112 L640 140 L0 140 Z" fill="var(--charcoal)"/>
    <path d="M0 26 C120 28 220 54 330 100 C440 138 560 120 640 124 L640 140 L0 140 Z" fill="var(--deep-blue)"/>
  </svg>
</section>

</body>
</html>
```